Business Card Design Project

Business card based on attached logo

Todd Merrick
Todd@lorvantest.com
877-514-9073 ext. 318
Www.LorvanTest.com

Industry/Entity Type

Business

```html
<!DOCTYPE html>
<html lang="en">
<head>
<meta charset="utf-8">
<title>LorvanTest Business Cards</title>
<link rel="stylesheet" href="https://fonts.googleapis.com/css2?family=Arimo:wght@400;700&display=swap">
<style>
  :root {
    --sheet: #8a8c8f;
    --white: #ffffff;
    --ink: #1f1f1f;
    --charcoal: #2a2a2a;
    --charcoal-light: #3c3c3c;
    --red: #e3262c;
    --red-deep: #c7202a;
    --red-dark: #a8161d;
    --card-edge: #5e5e5e;
  }
  * { box-sizing: border-box; margin: 0; padding: 0; }
  html, body {
    width: 1200px; height: 720px; overflow: hidden;
    background: var(--sheet);
    font-family: "Arimo", Arial, sans-serif;
  }
  .sheet { position: relative; width: 1200px; height: 720px; }

  .card {
    position: absolute; width: 564px; height: 320px;
    border-radius: 26px; overflow: hidden;
  }
  .card--contact { left: 24px; top: 27px; background: var(--white); }
  .card--white   { left: 609px; top: 27px; background: var(--white); border: 1px solid var(--card-edge); }
  .card--dark    { left: 24px; top: 372px; background: radial-gradient(ellipse at 50% 35%, var(--charcoal-light), var(--charcoal) 70%); }
  .card--red     { left: 609px; top: 372px; background: linear-gradient(135deg, var(--red) 0%, var(--red-deep) 60%, var(--red-dark) 100%); }

  .brand {
    position: absolute; display: flex; align-items: center; gap: 12px;
    font-weight: 700; letter-spacing: -1px; line-height: 1;
  }
  .brand__mark { width: 0.42em; height: 0.42em; background: var(--red); flex: none; margin-bottom: 0.5em; }
  .brand--center { left: 0; right: 0; justify-content: center; }
  .brand--ink   { color: var(--ink); }
  .brand--light { color: var(--white); }

  .card--contact .brand { top: 66px; font-size: 54px; }
  .card--white .brand   { top: 110px; font-size: 66px; }
  .card--dark .brand    { top: 118px; font-size: 66px; }
  .card--red .brand     { left: 36px; top: 42px; font-size: 66px; }
  .card--red .brand__mark { background: var(--white); }

  .swoosh { position: absolute; left: 0; top: 0; width: 564px; height: 320px; }

  .person {
    position: absolute; top: 196px; left: 0; right: 0; text-align: center;
    color: var(--red); font-size: 18px; letter-spacing: 0.5px;
  }
  .contact {
    position: absolute; left: 0; right: 0; text-align: center;
    color: var(--white); font-size: 16px;
    display: flex; justify-content: center; align-items: center; gap: 14px;
  }
  .contact--phone { top: 268px; }
  .contact--lines { top: 293px; }
  .contact__item { display: inline-flex; align-items: center; gap: 6px; }
  .contact__icon { width: 13px; height: 13px; }

  .site {
    position: absolute; font-size: 16px; letter-spacing: 2.6px;
  }
  .card--white .site { top: 280px; left: 0; right: 0; text-align: center; color: var(--ink); }
  .card--dark .site  { top: 280px; left: 0; right: 0; text-align: center; color: var(--white); }
  .card--red .site   { top: 292px; left: 36px; color: var(--white); }

  .faint-square {
    position: absolute; left: 398px; top: 152px; width: 170px; height: 170px;
    background: rgba(255, 255, 255, 0.14);
    border: 1px solid rgba(255, 255, 255, 0.12);
  }
</style>
</head>
<body>
<main class="sheet">

  <section class="card card--contact">
    <svg class="swoosh" viewBox="0 0 564 320" aria-hidden="true">
      <path d="M0 192 Q282 262 564 192 L564 320 L0 320 Z" fill="var(--red-deep)"/>
      <path d="M0 206 Q282 268 564 200 L564 320 L0 320 Z" fill="var(--charcoal)"/>
    </svg>
    <div class="brand brand--center brand--ink"><span>LorvanTest</span><span class="brand__mark"></span></div>
    <p class="person">TODD MERRICK</p>
    <p class="contact contact--phone">
      <span class="contact__item">
        <svg class="contact__icon" viewBox="0 0 16 16" aria-hidden="true"><path d="M3 1 L6 1 L7 5 L5 6.5 Q6.5 9.5 9.5 11 L11 9 L15 10 L15 13 Q15 15 13 15 Q1 14 1 3 Q1 1 3 1 Z" fill="var(--white)"/></svg>
        877-514-9073 ext. 318
      </span>
    </p>
    <p class="contact contact--lines">
      <span class="contact__item">
        <svg class="contact__icon" viewBox="0 0 16 16" aria-hidden="true"><rect x="1" y="3.5" width="14" height="10" rx="1" fill="var(--white)"/><path d="M1.5 4 L8 9 L14.5 4" stroke="var(--charcoal)" stroke-width="1.3" fill="none"/></svg>
        Todd@lorvantest.com
      </span>
      <span class="contact__item">
        <svg class="contact__icon" viewBox="0 0 16 16" aria-hidden="true"><g fill="none" stroke="var(--white)" stroke-width="1.3"><circle cx="8" cy="8" r="6.5"/><ellipse cx="8" cy="8" rx="3" ry="6.5"/><path d="M1.5 8 H14.5"/></g></svg>
        www.lorvantest.com
      </span>
    </p>
  </section>

  <section class="card card--white">
    <div class="brand brand--center brand--ink"><span>LorvanTest</span><span class="brand__mark"></span></div>
    <p class="site">www.lorvantest.com</p>
  </section>

  <section class="card card--dark">
    <div class="brand brand--center brand--light"><span>LorvanTest</span><span class="brand__mark"></span></div>
    <p class="site">www.lorvantest.com</p>
  </section>

  <section class="card card--red">
    <div class="faint-square"></div>
    <div class="brand brand--light"><span>LorvanTest</span><span class="brand__mark"></span></div>
    <p class="site">www.lorvantest.com</p>
  </section>

</main>
</body>
</html>
```